Church needs a street sign design

We're a small church located in Silicon Valley, California. Our website is https://www.vgtmarlowfield.org/ and our address is 4817 Ferrow Ave, San Jose, California, 95873. You can look up our location on Google Maps to see the sign from Street View. I have uploaded an image of the street sign as well. The marquee, the top section of the sign, and the separating line between them both will be removed. We're seeking a design for a new backlit acrylic insert that will go on the front of the light box and the back of the lightbox. The acrylic sign will fill the entire external frame. In the future, we may build a decorative wood frame around the structural legs, as visualized in one of the uploaded files. The church's brand colors are: #003366 (dark blue), #ff6600 (vibrant orange), #228b22 (forest green). I have also uploaded the church's logo assets. Our primary font is Montserrat and the secondary is Poppins. You can deviate from these colors/fonts if the sign is still coherent with the rest of our branding. Our branding values are mission, truth, passion, and community (please do not put those words on the sign! They are just intended to guide the look of the design). The sign dimensions are 96" by 47.5". Keep in mind that the sign will be backlit on a busy street side. It will also be positioned next to an old-looking church building. We do NOT want a sign that looks traditional, old, or antiquated. Instead, we want a modern-looking sign that pairs well with our old building while helping it look more modern too. We would also like the web address clearly visible on the sign: vgtmarlowfield.org. If you have any questions, just let me know!

```html
<!DOCTYPE html>
<html lang="en">
<head>
<meta charset="utf-8">
<title>Marlowfield Grace Church – Street Sign</title>
<link rel="stylesheet" href="https://fonts.googleapis.com/css2?family=Montserrat:wght@500;700;800&family=Poppins:wght@700&family=Oswald:wght@700&family=Great+Vibes&family=Yellowtail&display=swap">
<style>
  :root {
    --page-bg: #aab3bb;
    --navy: #1c2b57;
    --orange: #ff6a12;
    --white: #ffffff;
    --cream-top: #fbd3a0;
    --cream-bottom: #fff8d8;
    --sky-top: #9c6a55;
    --sky-mid: #e7955c;
    --sky-low: #ffb468;
  }
  * { margin: 0; padding: 0; box-sizing: border-box; }
  html, body {
    width: 980px;
    height: 1200px;
    overflow: hidden;
    background: var(--page-bg);
  }
  .sign {
    position: absolute;
    left: 50px;
    top: 380px;
    width: 880px;
    height: 440px;
    overflow: hidden;
    box-shadow: 0 14px 40px rgba(0, 0, 0, 0.28);
  }
  .sign__scene {
    position: absolute;
    inset: 0;
    background: linear-gradient(180deg, var(--sky-top) 0%, var(--sky-mid) 45%, var(--sky-low) 70%, #ff8a3c 85%);
  }
  .sign__hills {
    position: absolute;
    inset: 0;
    width: 880px;
    height: 440px;
  }
  .headline {
    position: absolute;
    left: 52px;
    top: 42px;
    font-family: "Montserrat", sans-serif;
    font-weight: 800;
    font-size: 76px;
    line-height: 64px;
    letter-spacing: -1px;
    background: linear-gradient(180deg, var(--cream-top), var(--cream-bottom));
    -webkit-background-clip: text;
    background-clip: text;
    color: transparent;
    filter: drop-shadow(0 2px 4px rgba(80, 40, 20, 0.25));
  }
  .subline {
    position: absolute;
    left: 50px;
    top: 186px;
    color: var(--navy);
  }
  .subline__script {
    display: block;
    font-family: "Great Vibes", cursive;
    font-size: 58px;
    line-height: 50px;
  }
  .subline__caps {
    display: block;
    font-family: "Oswald", sans-serif;
    font-weight: 700;
    font-size: 44px;
    line-height: 44px;
    margin-top: -6px;
  }
  .web-address {
    position: absolute;
    left: 58px;
    top: 352px;
    font-family: "Montserrat", sans-serif;
    font-weight: 700;
    font-size: 29px;
    letter-spacing: 1px;
    color: var(--white);
    text-shadow: 0 2px 3px rgba(0, 0, 0, 0.35);
  }
  .tagline {
    position: absolute;
    left: 582px;
    top: 304px;
    color: var(--white);
  }
  .tagline__caps {
    display: block;
    font-family: "Poppins", sans-serif;
    font-weight: 700;
    font-size: 33px;
    line-height: 40px;
    letter-spacing: -1px;
  }
  .tagline__script {
    display: block;
    font-family: "Yellowtail", cursive;
    font-size: 50px;
    line-height: 44px;
    color: var(--orange);
    margin-left: 38px;
  }
  .church-name {
    position: absolute;
    left: 648px;
    top: 40px;
    font-family: "Montserrat", sans-serif;
    font-weight: 500;
    color: var(--white);
  }
  .church-name__main {
    display: block;
    font-size: 25px;
    line-height: 28px;
  }
  .church-name__sub {
    display: block;
    font-size: 10.5px;
    line-height: 14px;
    letter-spacing: 1.6px;
  }
</style>
</head>
<body>
  <main class="sign">
    <div class="sign__scene" role="img" aria-label="Sunset sky over hills with three cross silhouettes"></div>
    <svg class="sign__hills" viewBox="0 0 880 440" aria-hidden="true">
      <path fill="var(--navy)" d="M0 372 C60 330 120 292 200 298 C260 302 300 322 360 318 C420 314 470 282 540 290 C600 296 640 300 700 280 C760 262 820 258 880 252 L880 440 L0 440 Z"/>
    </svg>

    <h1 class="headline">MAKING<br>DISCIPLES</h1>
    <p class="subline">
      <span class="subline__script">&amp; Helping</span>
      <span class="subline__caps">THE HELPLESS</span>
    </p>

    <p class="web-address">www.vgtmarlowfield.org</p>

    <p class="tagline">
      <span class="tagline__caps">FOR THE GLORY</span>
      <span class="tagline__script">of christ</span>
    </p>

    <p class="church-name">
      <span class="church-name__main">MARLOWFIELD</span>
      <span class="church-name__sub">GRACE CHURCH</span>
    </p>
  </main>
</body>
</html>
```